Blood Testing Health App

We are looking for a graphics designer to create a web app for us so that we may insert it into a health management website system.
For branding purposes we are at www.Vantiqor.com and we are revamping our website... Example of new colors attached.
How we work...
We are a blood testing company based in the USA.
We offer a blood testing service nationwide in the USA.
We allow customers to order tests directly from us, visit a lab, have their blood drawn, or submit a urine sample, the lab tests it and they send the results back to our computer system and we share it with the customer.
The benefits of this are the customer does not need to go to the doctor and pay for the doctors visit to order these tests, which save them money. The tests are cheaper than going through the doctor. The customer simply uses us to get the test and the results and they can then take the results to their doctor... this process has saved them money. Others may be interested in regular check ups for blood work etc... and this allows them to do it with out needing a doctor, or if you have no insurance, this is a cheaper option too. We are quicker than a doctor, customers do not need appointments etc.
Hopefully you now have a better understanding as to what we do.
Here is the spec.
The app screen size is 750 px wide by 700 px high. ( A pdf is attached to show where the app is going to go, it is on page 3 of the pdf) The customer will have the ability to scroll… therefore the length of the page can be longer.
The app will consist of the following sections
Entry Page –
This will be the first page the user sees upon opening the app. This will be where they are directed from to the sections of the app discussed below. This needs to be branded for VantiQor with a modern look.
1 – Order Test (Giving them the ability to purchase a blood test within the app)
2 – VantiQor Dashboard (A dashboard that has everything they could need to use our service_
How it works Section on entry page – this will be a simple set of graphics showing how the service works. We already have the graphics for this, they do not need to be built again. They are attached to this brief
Basic structure of sections –
Order Test –
This page contains all tests, filed in categories – and Sub categories – Each test needs a link to an Information section – Price – Buy Now – Cart Process
VantiQor Dashboard –
A page of icons along the top of the app
- My Confirmation
- My Nearest Lab
- My Receipt
- My Orders
- My Account
- My Results
- My Inbox
- Contact Us
Sections in more detail -
Order A Test –
Show all categories/ sub categories – There are 23 categories, 14 sub categories, and within these categories are 300 tests - Here is the information for the categories etc - http://www.vantiqor.com/panels.aspx?PanelGroupID=4 Just in case it helps :)
We need to present this in a graphic format that is spacious, modern (brimlake, kivvo web appearance is the direction we are going for) We need it to be clear and not overwhelming to the customer.
Functionality idea…
Customer clicks category/ subcategory and tests appear.
Customer sees small 35 word description. For more information the test opens into a lightbox or expand the container which ever graphic designer believes to be most visually appealing
Buy Now must always be visible, along with price of the test
Buying process explained – Customer clicks buy now –
They are then taken to a Review Order screen ( This contains Order summary and choose payment method – insert payment details )
– Confirm payment –
Confirmation screen appears, thanking them.
They are then taken to the VantiQor Dashboard...
VantiQor Dashboard –
"My Confirmation" - Print Confirmation Order (PDF is in brief, we want this web based not a pdf download)
"My Nearest Lab Location" - This does not need to be designed because the web developer has this part under control, but we do need the icon in the dashboard
"My Receipt" - Print receipt - This does not exist in our system yet. So we need to create this from scratch - It will need to have - The test they are purchasing and the amount of the test - The customers name - The order ID - Must provide printer friendly option too
"My Orders" - This will have a list of orders - At the end of each order will be a status update of either "Test results" "Open order"
A graphic table format would be perfect. This will be linked to relevant results if they have been received. I have also attached a version of what the customer currently sees on our website. We know it is nasty ;) We are redesigning... but the information is there for this section to help design it with the right info. If the results are ready it will say in this list.
"Results Ready" will be a link to show those results once the customer has clicked the link, and the results will appear in the app, under the icons. There must be a printer friendly version too.
"My Results" Developer will sort this page out but we need the icon... It will be exactly like my orders but only show test results
"My Account" - This will be a place for them to update their personal information - Name, DOB, Address, Email Address
"My Inbox" - An inbox interface - Our way of contacting the customer for promotions we are running etc – We need a design of how this screen will appear. We also need the icon in the dashboard to have a notification on it if there are messages in the customers inbox. A little red 1, or circle with number of messages in the inbox.
"Customer Service" - This does not need to be designed because the web developer has this part under control, but we do need the icon in the dashboard
Icons appear along the top of app ( example - Mac icons/ iphone app icons) When the customer clicks an icon the content always appears below the icons
Here is more information for the icons and what should appear when each icon is clicked.
Screens to be designed –
Entry Page
Order A Test Page
Review Order Screen/Payment Screen - Show a lightbox that shows payment has been confirmed. Customer clicks close and are on the Confirmation Screen
VantiQor Dashboard - Screens mentioned in detail above
We can't wait to see your designs!
Please email any questions.
Hi all this is the first time we have used pixel harbor and understand the budget was too low for this project. We have now increased the budget to $2,000 and extended the deadline by another week
Hi all we are receiving some really great designs. I just added an example of the space that the web app will be going into... It is called "morvelapp.pdf"
Hi guys updated the brief. Hopefully this will help with the dashboard part of the design

```html
<!DOCTYPE html>
<html lang="en">
<head>
<meta charset="utf-8">
<title>VantiQor – Shopping Cart</title>
<link href="https://fonts.googleapis.com/css2?family=Open+Sans:wght@300;400;600;700&display=swap" rel="stylesheet">
<style>
  :root{
    --green:#7dc035;
    --green-dark:#6aa82a;
    --panel:#ebebeb;
    --white:#ffffff;
    --head-dark:#545a55;
    --ink:#222222;
    --muted:#333333;
    --link:#1f73c9;
    --field:#ececec;
    --line:#e4e4e4;
    --red:#e8401c;
    --orange-top:#ff7a1a;
    --orange-bot:#f24a05;
    --blue-top:#4a9be6;
    --blue-bot:#1e72cf;
    --btn-grey-top:#fafafa;
    --btn-grey-bot:#e6e6e6;
  }
  *{box-sizing:border-box;margin:0;padding:0}
  html,body{width:1200px;height:1163px;overflow:hidden;background:var(--white);font-family:"Open Sans",Arial,sans-serif;color:var(--ink)}
  .app{position:relative;width:1200px;height:1163px}

  .brand{position:absolute;left:29px;top:58px;display:flex;align-items:center;gap:18px}
  .brand-mark{width:56px;height:56px;background:var(--green);border-radius:6px}
  .brand-name{font-size:64px;font-weight:400;color:#2b2b2b;letter-spacing:1px;line-height:1}

  .nav-btn{position:absolute;top:45px;width:207px;height:104px;border:1px solid #dcdcdc;border-radius:8px;
    background:linear-gradient(var(--btn-grey-top),var(--btn-grey-bot));display:flex;flex-direction:column;
    align-items:center;justify-content:center;gap:10px;color:var(--green);font-size:17px}
  .nav-order{left:534px}
  .nav-dashboard{left:762px}

  .social{position:absolute;top:101px;left:1010px;display:flex;gap:10px}
  .social span{width:44px;height:44px;border-radius:50%;background:var(--green);display:block}

  .cart-panel{position:absolute;left:29px;top:190px;width:1139px;height:608px;background:var(--panel);border-radius:16px}
  .cart-card{position:absolute;left:17px;top:18px;width:1103px;height:416px;background:var(--white);border-radius:14px;overflow:hidden}
  .cart-title{height:75px;background:var(--green);color:var(--white);font-size:30px;font-weight:300;padding-left:24px;line-height:75px}
  .cart-head{position:relative;height:58px;background:var(--head-dark);color:var(--white);font-size:21px}
  .cart-head span,.cart-row .cell{position:absolute}
  .cart-head span{top:14px}
  .col-name{left:24px}.col-price{left:572px}.col-qty{left:706px}.col-sub{left:821px}.col-remove{left:978px}

  .cart-row{position:relative;height:136px;border-bottom:1px solid var(--line)}
  .cart-row:last-child{border-bottom:none}
  .test-info{position:absolute;left:25px;top:28px;width:520px}
  .test-name{color:var(--link);font-size:21px;line-height:30px}
  .test-desc{font-size:17px;line-height:23px;color:var(--muted)}
  .cart-row .price,.cart-row .subtotal{top:31px;font-size:17px}
  .price{left:573px}.subtotal{left:822px}
  .qty{left:709px;top:27px;width:74px;height:35px;background:var(--field);border-radius:3px;font-size:17px;padding:6px 14px}
  .remove{left:1004px;top:29px}

  .discount{position:absolute;left:17px;top:463px;width:623px;height:115px;background:var(--white);border-radius:16px}
  .discount-label{position:absolute;left:25px;top:20px;font-size:22px;font-weight:600;color:#444}
  .discount-input{position:absolute;left:24px;top:48px;width:402px;height:46px;background:#f3f3f3;border:1px solid #e2e2e2;border-radius:4px}
  .btn{position:absolute;display:flex;align-items:center;justify-content:center;color:var(--white);font-weight:700;text-align:center;border-radius:5px}
  .btn-apply{left:439px;top:48px;width:152px;height:46px;font-size:22px;font-weight:600;gap:14px;
    background:linear-gradient(var(--orange-top),var(--orange-bot));border:2px solid #ff9a5a}
  .btn-continue{left:685px;top:464px;width:208px;height:90px;font-size:21px;line-height:24px;
    background:linear-gradient(var(--orange-top),var(--orange-bot));border:2px solid #ff9a5a}
  .btn-checkout{left:910px;top:464px;width:208px;height:90px;font-size:21px;line-height:24px;
    background:linear-gradient(var(--blue-top),var(--blue-bot));border:2px solid #7bb8f0}
</style>
</head>
<body>
<div class="app">
  <div class="brand">
    <span class="brand-mark"></span>
    <span class="brand-name">VantiQor</span>
  </div>

  <a class="nav-btn nav-order">
    <svg width="58" height="38" viewBox="0 0 58 38"><rect x="8" y="2" width="42" height="28" rx="3" fill="var(--green)"/><rect x="2" y="31" width="54" height="5" rx="2" fill="var(--green)"/><path d="M20 22 L36 10" stroke="#fff" stroke-width="3"/></svg>
    <span>ORDER A TEST</span>
  </a>
  <a class="nav-btn nav-dashboard">
    <svg width="44" height="42" viewBox="0 0 44 42"><rect x="12" y="2" width="30" height="26" rx="2" fill="none" stroke="var(--green)" stroke-width="4"/><rect x="2" y="14" width="30" height="26" rx="2" fill="var(--white)" stroke="var(--green)" stroke-width="4"/><rect x="2" y="14" width="30" height="7" fill="var(--green)"/></svg>
    <span>DASHBOARD</span>
  </a>

  <div class="social"><span></span><span></span><span></span></div>

  <section class="cart-panel">
    <div class="cart-card">
      <h1 class="cart-title">SHOPPING CART</h1>
      <div class="cart-head">
        <span class="col-name">Test Name</span>
        <span class="col-price">Price</span>
        <span class="col-qty">Qty</span>
        <span class="col-sub">Subtotal</span>
        <span class="col-remove">Remove</span>
      </div>
      <div class="cart-row">
        <div class="test-info">
          <div class="test-name">COMPREHENSIVE Erectile Dysfunction Profile</div>
          <p class="test-desc">Lorem ipsum dolor sit amet, consectetur adipisicing elit, sed do eiusmod tempor incididunt ut labore et ...</p>
        </div>
        <span class="cell price">$75.00</span>
        <span class="cell qty">1</span>
        <span class="cell subtotal">$75.00</span>
        <svg class="cell remove" width="30" height="30" viewBox="0 0 30 30"><circle cx="15" cy="15" r="14" fill="var(--red)"/><path d="M10 10 L20 20 M20 10 L10 20" stroke="#fff" stroke-width="3.2" stroke-linecap="round"/></svg>
      </div>
      <div class="cart-row">
        <div class="test-info">
          <div class="test-name">COMPREHENSIVE Erectile Dysfunction Profile</div>
          <p class="test-desc">Lorem ipsum dolor sit amet, consectetur adipisicing elit, sed do eiusmod tempor incididunt ut labore et ...</p>
        </div>
        <span class="cell price">$75.00</span>
        <span class="cell qty">1</span>
        <span class="cell subtotal">$75.00</span>
        <svg class="cell remove" width="30" height="30" viewBox="0 0 30 30"><circle cx="15" cy="15" r="14" fill="var(--red)"/><path d="M10 10 L20 20 M20 10 L10 20" stroke="#fff" stroke-width="3.2" stroke-linecap="round"/></svg>
      </div>
    </div>

    <div class="discount">
      <span class="discount-label">Discount Code</span>
      <span class="discount-input"></span>
      <a class="btn btn-apply">APPLY
        <svg width="24" height="24" viewBox="0 0 24 24"><circle cx="12" cy="12" r="11" fill="#5a2300"/><path d="M6 12 H17 M13 8 L17 12 L13 16" stroke="#fff" stroke-width="2.4" fill="none" stroke-linecap="round" stroke-linejoin="round"/></svg>
      </a>
    </div>

    <a class="btn btn-continue">CONTINUE<br>SHOPPING</a>
    <a class="btn btn-checkout">PROCEED TO<br>CHECKOUT</a>
  </section>
</div>
</body>
</html>
```